My project benefits Military, First Responders, Police, Fire, and Educators.

Contact Information for Business Card

2 Sided appointment card. Visual side will have my head shot with "Brisk Lantern" in a bold graffic/text. I am picturing maybe the headshot applied to a filter that has a matrix effect where the picture is made up of data/numbers flowing vertically through the photo. I am of course open to other concepts as well. Side two will have contact info presented in an attractive visual complimenting the front.

```html
<!DOCTYPE html>
<html lang="en">
<head>
<meta charset="utf-8">
<title>Brisk Lantern – Appointment Card</title>
<link href="https://fonts.googleapis.com/css2?family=Open+Sans:wght@400;600&display=swap" rel="stylesheet">
<style>
  :root {
    --page-bg: #e9e7e4;
    --card-dark: #1f2a33;
    --card-light: #ffffff;
    --brand-mint: #2ee6a6;
    --text-light: #ffffff;
    --text-muted: #4a4f54;
    --rule-grey: #a9adb0;
    --photo-warm: #b88a6c;
    --photo-mid: #6f7f95;
    --photo-suit: #1d2b45;
  }
  * { margin: 0; padding: 0; box-sizing: border-box; }
  html, body {
    width: 1200px; height: 900px; overflow: hidden;
    background: var(--page-bg);
    font-family: "Open Sans", Arial, sans-serif;
  }
  .canvas { position: relative; width: 1200px; height: 900px; }

  .card {
    position: absolute;
    height: 342px;
    box-shadow: 0 6px 18px rgba(0,0,0,0.18);
    overflow: hidden;
  }
  .card-front { left: 238px; top: 62px; width: 556px; background: var(--card-dark); }
  .card-back { left: 457px; top: 519px; width: 560px; background: var(--card-light); }

  /* Front */
  .headshot {
    position: absolute; left: 0; top: 20px; width: 276px; height: 322px;
    border-radius: 120px 120px 0 0;
    background: linear-gradient(180deg, var(--photo-warm) 0%, var(--photo-mid) 55%, var(--photo-suit) 78%, var(--photo-suit) 100%);
  }
  .front-brand {
    position: absolute; right: 26px; top: 76px; width: 200px; height: 130px;
    display: flex; align-items: center; justify-content: center;
  }
  .brand-name {
    color: var(--brand-mint); font-weight: 600; font-size: 26px;
    letter-spacing: 0.5px; white-space: nowrap;
  }
  .identity {
    position: absolute; right: 24px; top: 188px; text-align: right;
    color: var(--text-light);
  }
  .identity .person-name { font-size: 18px; font-weight: 600; line-height: 24px; }
  .identity .person-role { font-size: 14px; line-height: 18px; }
  .contact-list {
    position: absolute; right: 24px; top: 252px; list-style: none;
    color: var(--text-light); font-size: 14.5px; text-align: right;
  }
  .contact-list li {
    display: flex; justify-content: flex-end; align-items: center;
    gap: 6px; line-height: 20.5px;
  }
  .contact-list svg { width: 11px; height: 11px; fill: var(--text-light); }

  /* Back */
  .back-band {
    position: absolute; left: 0; top: 0; width: 100%; height: 204px;
    background: var(--card-dark);
  }
  .back-band .brand-name {
    position: absolute; left: 0; top: 130px; width: 100%; text-align: center;
    font-size: 34px; font-weight: 400; letter-spacing: 1.5px; text-transform: uppercase;
    line-height: 44px;
  }
  .appointment-line {
    position: absolute; left: 78px; width: 404px; height: 0;
    border-top: 1.5px solid var(--rule-grey);
  }
  .line-date { top: 251px; }
  .line-time { top: 282px; }
  .notice {
    position: absolute; left: 0; top: 306px; width: 100%; text-align: center;
    color: var(--text-muted); font-size: 15px;
  }
</style>
</head>
<body>
<div class="canvas">

  <section class="card card-front">
    <div class="headshot" role="img" aria-label="Head shot of the managing director in a dark suit and striped tie"></div>

    <div class="front-brand">
      <span class="brand-name">Brisk Lantern</span>
    </div>

    <div class="identity">
      <p class="person-name">Daniel Reyes</p>
      <p class="person-role">Managing Director</p>
    </div>

    <ul class="contact-list">
      <li>044-210 555 318
        <svg viewBox="0 0 24 24" aria-hidden="true"><path d="M6.6 10.8a15.1 15.1 0 0 0 6.6 6.6l2.2-2.2a1 1 0 0 1 1-.25 11.4 11.4 0 0 0 3.6.57 1 1 0 0 1 1 1V20a1 1 0 0 1-1 1A17 17 0 0 1 3 4a1 1 0 0 1 1-1h3.5a1 1 0 0 1 1 1c0 1.25.2 2.45.57 3.57a1 1 0 0 1-.25 1z"/></svg>
      </li>
      <li>hello@brisklantern.com
        <svg viewBox="0 0 24 24" aria-hidden="true"><path d="M2 5h20v14H2z M4 7v.5l8 5 8-5V7z" fill-rule="evenodd"/></svg>
      </li>
      <li>www.brisklantern.com
        <svg viewBox="0 0 24 24" aria-hidden="true"><path d="M12 2a10 10 0 1 0 0 20 10 10 0 0 0 0-20zm6.9 6h-3a15 15 0 0 0-1.3-3.9A8 8 0 0 1 18.9 8zM12 4c.8 1.2 1.5 2.5 1.9 4h-3.8c.4-1.5 1.1-2.8 1.9-4zM4.3 14a8 8 0 0 1 0-4h3.4a16 16 0 0 0 0 4zm.8 2h3a15 15 0 0 0 1.3 3.9A8 8 0 0 1 5.1 16zm3-8h-3a8 8 0 0 1 4.3-3.9A15 15 0 0 0 8.1 8zM12 20c-.8-1.2-1.5-2.5-1.9-4h3.8c-.4 1.5-1.1 2.8-1.9 4zm2.3-6H9.7a14 14 0 0 1 0-4h4.6a14 14 0 0 1 0 4zm.3 5.9a15 15 0 0 0 1.3-3.9h3a8 8 0 0 1-4.3 3.9zM16.3 14a16 16 0 0 0 0-4h3.4a8 8 0 0 1 0 4z"/></svg>
      </li>
    </ul>
  </section>

  <section class="card card-back">
    <div class="back-band">
      <span class="brand-name">Brisk Lantern</span>
    </div>
    <div class="appointment-line line-date"></div>
    <div class="appointment-line line-time"></div>
    <p class="notice">If unable to keep appointment, kindly give 24hrs notice.</p>
  </section>

</div>
</body>
</html>
```